Stonebrace Business Card Design

The Stonebrace Co is an aggregate (crushing) equipment dealer serving Western Canadian provinces. Stonebrace is a distributor of aggregate equipment for different manufacturers.

We are looking to change and update the existing business card which has been used since the existence of the company. A copy of existing card has been attached for reference. The Stonebrace Co logo we want to remain the same and we want the green color to remain the same.

We are wanting something new with a different look. A refreshing card to show a new modern and updated look. No longer wanting to have the manufacturers on the back of the card but something more like our logo on the back of the card with a statement like "Crushing Solutions"

ideas could be:
- card can be different colors on front and back
- front or reverse of the card could possibly be the green color with the logo in black

Target Market(s)

Owners of Aggregate/Crushing companies

Contact Information for Business Card

see above

Requirements
Must have
• - logo to remain same along with same font within logo
• - green color to remain same
Nice to have
• as noted above under project description
Should not have

```html
<!DOCTYPE html>
<html lang="en">
<head>
<meta charset="utf-8">
<title>The Stonebrace Co — Business Card</title>
<link href="https://fonts.googleapis.com/css2?family=Arimo:wght@400;700&display=swap" rel="stylesheet">
<style>
  :root {
    --stage: #1a1a1a;
    --card-white: #ffffff;
    --brand-green: #878a0b;
    --brand-green-soft: #9c9d2e;
    --ink: #1c1c1c;
    --rule: #9a9a9a;
    --reverse-name: #e4e4d6;
    --reverse-tag: #ffffff;
  }
  * { margin: 0; padding: 0; box-sizing: border-box; }
  html, body {
    width: 1200px; height: 900px; overflow: hidden;
    background: var(--stage);
    font-family: "Arimo", Arial, sans-serif;
  }
  .stage { position: relative; width: 1200px; height: 900px; }

  .card {
    position: absolute; top: 170px;
    width: 347px; height: 561px;
    box-shadow: 3px 3px 6px rgba(0,0,0,0.55);
  }
  .card--front { left: 259px; background: var(--card-white); }
  .card--back { left: 631px; background: var(--brand-green); overflow: hidden; }

  /* Front */
  .brand-mark {
    position: absolute; left: 50%; top: 98px;
    width: 64px; height: 64px; margin-left: -32px;
    border-radius: 50%; background: var(--brand-green);
  }
  .brand-name {
    position: absolute; left: 0; right: 0; top: 184px;
    text-align: center; font-weight: 700; font-size: 24px;
    letter-spacing: 0.5px; color: var(--ink);
  }
  .holder {
    position: absolute; left: 0; right: 0; top: 314px;
    text-align: center; font-size: 21px; color: var(--brand-green);
    letter-spacing: 0.3px;
  }
  .rule {
    position: absolute; left: 82px; width: 182px; height: 1px;
    background: var(--rule);
  }
  .rule--top { top: 349px; }
  .rule--bottom { top: 411px; }
  .address {
    position: absolute; left: 0; right: 0; top: 360px;
    text-align: center; font-size: 16px; line-height: 20px; color: var(--ink);
    font-style: normal;
  }
  .contacts {
    position: absolute; left: 0; right: 0; top: 424px;
    text-align: center; font-size: 16px; line-height: 20px; color: var(--ink);
    list-style: none;
  }
  .contacts .label { color: var(--brand-green); font-weight: 700; }
  .contacts .web { color: var(--brand-green); }

  /* Back */
  .back-field {
    position: absolute; inset: 0;
    background: linear-gradient(160deg, var(--brand-green-soft) 0%, var(--brand-green) 55%, var(--brand-green-soft) 100%);
  }
  .back-name {
    position: absolute; left: 0; right: 0; top: 446px;
    text-align: center; font-weight: 700; font-size: 24px;
    letter-spacing: 0.5px; color: var(--reverse-name);
  }
  .back-tagline {
    position: absolute; left: 0; right: 0; top: 492px;
    text-align: center; font-weight: 700; font-size: 16px;
    letter-spacing: 1.6px; color: var(--reverse-tag);
  }
</style>
</head>
<body>
<main class="stage">
  <section class="card card--front" aria-label="Card front">
    <span class="brand-mark" aria-hidden="true"></span>
    <div class="brand-name">THE STONEBRACE CO.</div>
    <div class="holder">DALE MORROW</div>
    <span class="rule rule--top"></span>
    <address class="address">2218-48B Avenue<br>Camrose, Alberta T4V 1K9</address>
    <span class="rule rule--bottom"></span>
    <ul class="contacts">
      <li><span class="label">P:</span> 780.555.0143(Direct)</li>
      <li><span class="label">P:</span> 780.555.0178</li>
      <li><span class="label">F:</span> 780.555.0192</li>
      <li><span class="label">E:</span> dale@stonebr.com</li>
      <li class="web">www.stonebrace.ca</li>
    </ul>
  </section>

  <section class="card card--back" aria-label="Card back">
    <div class="back-field" role="img" aria-label="Large faint brand symbol pattern in lighter olive green"></div>
    <div class="back-name">THE STONEBRACE CO.</div>
    <div class="back-tagline">CRUSHING SOLUTIONS</div>
  </section>
</main>
</body>
</html>
```